Four in One (Flexible infographic for Content Management Industry)

See attachment.
A graphic depicting 4 products, where each can stand on its own and each can be combined with others, but where, if all are taken together, the best result is achieved (the "super product").
Intended use is web. See attached file as an example.
The most basic idea is as the attached diagram shows, where 4 rectangles are arranged in a quadrangle, with a middle rectangle in the center representing the combined 4 products. This concept is fine except it is a bit too obvious as it stands. We are looking for either a variation of this or another concept.
The audience is technical + professional + enterprise - NOT consumers. Hence the design should be conservative in nature.
We are aware of tools like as Canva or Pictogram where such graphics are available, but we are looking for something with a bit more imagination and flexibility.
This graphic should be targeted to web sites and be delivered with vector-based (SVG) graphics.

```html
<!DOCTYPE html>
<html lang="en">
<head>
<meta charset="utf-8">
<title>Four in One – Super Product Infographic</title>
<link rel="stylesheet" href="https://fonts.googleapis.com/css2?family=Bebas+Neue&family=Poppins:wght@300;400;700;800&display=swap">
<style>
  :root {
    --page-bg: #868686;
    --board-bg: #efefef;
    --hub-ring: #c9c7c9;

    --doc-tile: #fd4141;
    --doc-band: #c22e2f;
    --doc-edge: #ff9c9c;
    --doc-tick: #66dd3f;

    --sec-tile: #40fde2;
    --sec-band: #139a88;
    --sec-edge: #a9fff2;
    --sec-head: #0e5b52;
    --sec-tick: #6a30dc;

    --erp-tile: #7b30ff;
    --erp-band: #5b21c6;
    --erp-edge: #c3a4ff;
    --erp-tick: #38cbee;

    --dig-tile: #8ffd40;
    --dig-band: #53921f;
    --dig-edge: #d2ffad;
    --dig-head: #1f3a0b;
    --dig-tick: #ee2121;

    --hub-orange: #f6a800;
    --hub-dark: #3a2400;
    --white: #ffffff;
  }
  * { box-sizing: border-box; margin: 0; padding: 0; }
  html, body { width: 1200px; height: 1200px; overflow: hidden; }
  body {
    background: var(--page-bg);
    font-family: "Poppins", sans-serif;
    position: relative;
  }
  .board {
    position: absolute; left: 0; top: 176px;
    width: 1200px; height: 848px;
    background: linear-gradient(135deg, #e4e4e4 0%, #f7f7f7 30%, #e9e9e9 55%, #f8f8f8 80%, #e6e6e6 100%);
    overflow: hidden;
  }
  .hub-backdrop {
    position: absolute; left: 380px; top: 203px;
    width: 442px; height: 442px; border-radius: 50%;
    background: var(--hub-ring);
  }
  .module { position: absolute; height: 308px; }
  .module__band {
    position: absolute; inset: 0;
    border-radius: 0 22px 22px 0;
  }
  .module__tile {
    position: absolute; left: 0; top: 0; bottom: 0; width: 262px;
    border-radius: 30px; border: 2px solid;
    display: flex; flex-direction: column; align-items: center;
  }
  .module__icon {
    margin-top: 44px; width: 128px; height: 128px; border-radius: 14px;
  }
  .module__title {
    font-family: "Bebas Neue", sans-serif;
    font-size: 36px; line-height: 35px; text-align: center;
    margin-top: 26px; letter-spacing: 0;
  }
  .module__body {
    position: absolute; color: var(--white);
  }
  .module__intro {
    font-weight: 300; font-size: 14.2px; line-height: 17.8px;
  }
  .feature-list { list-style: none; margin-top: 20px; }
  .feature-list li {
    display: flex; align-items: flex-start; gap: 9px;
    font-weight: 700; font-size: 14.2px; line-height: 15px;
    margin-bottom: 20px;
  }
  .feature-list svg { flex: none; width: 16px; height: 16px; margin-top: 0; }

  .module--doc { left: 0; top: 42px; width: 593px; }
  .module--doc .module__band { background: var(--doc-band); }
  .module--doc .module__tile { background: var(--doc-tile); border-color: var(--doc-edge); color: var(--white); }
  .module--doc .module__icon { background: linear-gradient(160deg, #f4d560, #f2f2f2 60%, #2c2c2c); }
  .module--doc .module__body { left: 286px; top: 40px; width: 290px; }

  .module--sec { left: 623px; top: 42px; width: 577px; }
  .module--sec .module__band { background: var(--sec-band); border-radius: 0 0 0 0; }
  .module--sec .module__tile { background: var(--sec-tile); border-color: var(--sec-edge); color: var(--sec-head); }
  .module--sec .module__icon { background: linear-gradient(160deg, #f2f2f2, #fde27a 50%, #4a86c8); }
  .module--sec .module__body { left: 286px; top: 51px; width: 240px; }
  .module--sec .feature-list { margin-top: 22px; }
  .module--sec .feature-list li { margin-bottom: 14px; }

  .module--erp { left: 0; top: 481px; width: 597px; height: 310px; }
  .module--erp .module__band { background: var(--erp-band); }
  .module--erp .module__tile { background: var(--erp-tile); border-color: var(--erp-edge); color: var(--white); }
  .module--erp .module__icon { background: linear-gradient(160deg, #2ec4f0, #ececec 50%, #f0c800); }
  .module--erp .module__body { left: 287px; top: 41px; width: 245px; }
  .module--erp .feature-list { margin-top: 22px; }

  .module--dig { left: 623px; top: 481px; width: 577px; height: 309px; }
  .module--dig .module__band { background: var(--dig-band); border-radius: 0 0 0 0; }
  .module--dig .module__tile { background: var(--dig-tile); border-color: var(--dig-edge); color: var(--dig-head); }
  .module--dig .module__icon { background: linear-gradient(160deg, #f6a53a, #fde9b5 50%, #2d6c8c); }
  .module--dig .module__body { left: 291px; top: 38px; width: 260px; }
  .module--dig .feature-list { margin-top: 20px; }
  .module--dig .feature-list li { margin-bottom: 14px; line-height: 14.5px; }

  .hub {
    position: absolute; left: 473px; top: 296px;
    width: 256px; height: 256px; border-radius: 50%;
    background: var(--white);
    box-shadow: 0 4px 14px rgba(0,0,0,0.18);
  }
  .hub__core {
    position: absolute; left: 11px; top: 11px; width: 234px; height: 234px;
    border-radius: 50%;
    background: radial-gradient(circle at 42% 38%, #f8ad00 0%, #f6a800 58%, #e08c00 70%, var(--hub-dark) 92%);
    display: flex; flex-direction: column; align-items: center; justify-content: center;
  }
  .hub__title {
    font-family: "Bebas Neue", sans-serif; font-size: 37px; line-height: 1;
    color: #2a1800; margin-top: 4px;
  }
  .hub__rule { width: 41px; height: 3px; background: var(--white); margin-top: 10px; }
</style>
</head>
<body>
  <main class="board">
    <div class="hub-backdrop"></div>

    <section class="module module--doc">
      <div class="module__band"></div>
      <div class="module__tile">
        <div class="module__icon" role="img" aria-label="Illustration of a person linked by arrows to a document and a gear"></div>
        <h2 class="module__title">Document<br>Management</h2>
      </div>
      <div class="module__body">
        <p class="module__intro">Streamline document organization, access, and collaboration with easier file storage and sharing, leading to more efficient workflows.</p>
        <ul class="feature-list">
          <li><svg viewBox="0 0 16 16"><circle cx="8" cy="8" r="8" fill="var(--doc-tick)"/><path d="M4.5 8.2l2.3 2.2 4.6-4.6" stroke="#fff" stroke-width="1.8" fill="none" stroke-linecap="round" stroke-linejoin="round"/></svg>Centralized Document Control</li>
          <li><svg viewBox="0 0 16 16"><circle cx="8" cy="8" r="8" fill="var(--doc-tick)"/><path d="M4.5 8.2l2.3 2.2 4.6-4.6" stroke="#fff" stroke-width="1.8" fill="none" stroke-linecap="round" stroke-linejoin="round"/></svg>Collaborative Workspace<br>Integration</li>
          <li><svg viewBox="0 0 16 16"><circle cx="8" cy="8" r="8" fill="var(--doc-tick)"/><path d="M4.5 8.2l2.3 2.2 4.6-4.6" stroke="#fff" stroke-width="1.8" fill="none" stroke-linecap="round" stroke-linejoin="round"/></svg>Automated Compliance</li>
          <li><svg viewBox="0 0 16 16"><circle cx="8" cy="8" r="8" fill="var(--doc-tick)"/><path d="M4.5 8.2l2.3 2.2 4.6-4.6" stroke="#fff" stroke-width="1.8" fill="none" stroke-linecap="round" stroke-linejoin="round"/></svg>Check 4</li>
        </ul>
      </div>
    </section>

    <section class="module module--sec">
      <div class="module__band" style="border-radius:0 22px 22px 0"></div>
      <div class="module__tile">
        <div class="module__icon" role="img" aria-label="Illustration of a document folder with a padlock shield"></div>
        <h2 class="module__title">Security and<br>Compliance</h2>
      </div>
      <div class="module__body">
        <p class="module__intro">Benefit from tailored cloud solutions, secure data storage, and expert disaster recovery planning for reliable and scalable IT operations.</p>
        <ul class="feature-list">
          <li><svg viewBox="0 0 16 16"><circle cx="8" cy="8" r="8" fill="var(--sec-tick)"/><path d="M4.5 8.2l2.3 2.2 4.6-4.6" stroke="#fff" stroke-width="1.8" fill="none" stroke-linecap="round" stroke-linejoin="round"/></svg>Custom Cloud Solutions</li>
          <li><svg viewBox="0 0 16 16"><circle cx="8" cy="8" r="8" fill="var(--sec-tick)"/><path d="M4.5 8.2l2.3 2.2 4.6-4.6" stroke="#fff" stroke-width="1.8" fill="none" stroke-linecap="round" stroke-linejoin="round"/></svg>Secure Data Storage</li>
          <li><svg viewBox="0 0 16 16"><circle cx="8" cy="8" r="8" fill="var(--sec-tick)"/><path d="M4.5 8.2l2.3 2.2 4.6-4.6" stroke="#fff" stroke-width="1.8" fill="none" stroke-linecap="round" stroke-linejoin="round"/></svg>Expert Disaster Recovery</li>
          <li><svg viewBox="0 0 16 16"><circle cx="8" cy="8" r="8" fill="var(--sec-tick)"/><path d="M4.5 8.2l2.3 2.2 4.6-4.6" stroke="#fff" stroke-width="1.8" fill="none" stroke-linecap="round" stroke-linejoin="round"/></svg>Check 4</li>
        </ul>
      </div>
    </section>

    <section class="module module--erp">
      <div class="module__band"></div>
      <div class="module__tile">
        <div class="module__icon" role="img" aria-label="Illustration of an ERP gear chip with connected nodes"></div>
        <h2 class="module__title">Enterprise<br>Resource Planning</h2>
      </div>
      <div class="module__body">
        <p class="module__intro">Streamline document organization, access, and collaboration with easier file storage and sharing, leading to more efficient workflows.</p>
        <ul class="feature-list">
          <li><svg viewBox="0 0 16 16"><circle cx="8" cy="8" r="8" fill="var(--erp-tick)"/><path d="M4.5 8.2l2.3 2.2 4.6-4.6" stroke="#fff" stroke-width="1.8" fill="none" stroke-linecap="round" stroke-linejoin="round"/></svg>Integrated Business Processes</li>
          <li><svg viewBox="0 0 16 16"><circle cx="8" cy="8" r="8" fill="var(--erp-tick)"/><path d="M4.5 8.2l2.3 2.2 4.6-4.6" stroke="#fff" stroke-width="1.8" fill="none" stroke-linecap="round" stroke-linejoin="round"/></svg>Enhanced Decision-Making</li>
          <li><svg viewBox="0 0 16 16"><circle cx="8" cy="8" r="8" fill="var(--erp-tick)"/><path d="M4.5 8.2l2.3 2.2 4.6-4.6" stroke="#fff" stroke-width="1.8" fill="none" stroke-linecap="round" stroke-linejoin="round"/></svg>Productivity Improvement</li>
          <li><svg viewBox="0 0 16 16"><circle cx="8" cy="8" r="8" fill="var(--erp-tick)"/><path d="M4.5 8.2l2.3 2.2 4.6-4.6" stroke="#fff" stroke-width="1.8" fill="none" stroke-linecap="round" stroke-linejoin="round"/></svg>Check 4</li>
        </ul>
      </div>
    </section>

    <section class="module module--dig">
      <div class="module__band" style="border-radius:0 22px 22px 0"></div>
      <div class="module__tile">
        <div class="module__icon" role="img" aria-label="Illustration of a laptop showing a code window and documents"></div>
        <h2 class="module__title">Digitital<br>Transformation</h2>
      </div>
      <div class="module__body">
        <p class="module__intro">Turn scanned documents into easily searchable digital archives, boosting efficiency and accessibility.</p>
        <ul class="feature-list">
          <li><svg viewBox="0 0 16 16"><circle cx="8" cy="8" r="8" fill="var(--dig-tick)"/><path d="M4.5 8.2l2.3 2.2 4.6-4.6" stroke="#fff" stroke-width="1.8" fill="none" stroke-linecap="round" stroke-linejoin="round"/></svg>Instant searchable Archives<br>with OCR</li>
          <li><svg viewBox="0 0 16 16"><circle cx="8" cy="8" r="8" fill="var(--dig-tick)"/><path d="M4.5 8.2l2.3 2.2 4.6-4.6" stroke="#fff" stroke-width="1.8" fill="none" stroke-linecap="round" stroke-linejoin="round"/></svg>Automated Document<br>Classification</li>
          <li><svg viewBox="0 0 16 16"><circle cx="8" cy="8" r="8" fill="var(--dig-tick)"/><path d="M4.5 8.2l2.3 2.2 4.6-4.6" stroke="#fff" stroke-width="1.8" fill="none" stroke-linecap="round" stroke-linejoin="round"/></svg>TeamPortal and Cloud Blob<br>Ready</li>
          <li><svg viewBox="0 0 16 16"><circle cx="8" cy="8" r="8" fill="var(--dig-tick)"/><path d="M4.5 8.2l2.3 2.2 4.6-4.6" stroke="#fff" stroke-width="1.8" fill="none" stroke-linecap="round" stroke-linejoin="round"/></svg>Check 4</li>
        </ul>
      </div>
    </section>

    <div class="hub">
      <div class="hub__core">
        <h1 class="hub__title">Super Product</h1>
        <span class="hub__rule"></span>
      </div>
    </div>
  </main>
</body>
</html>
```